RM Installations Web Site Design

Need a basic site to show clients a little about what we do. We are a custom audio video company in the high-end residential market. Need a few basic but professional pages to show past projects and products we sell. No e-commerce. Should include my new logo from MarkBazaar.

Industry/Entity Type

Residential

Number of Pages Required

2 page

Font styles to use
Serif
Sans Serif

Colors
f78f20

Requirements
Must have
• Company Logo, Send feedback page
Nice to have
• I have no ideas about design, but I do know what I like and dislike when I see it.

```html
<!DOCTYPE html>
<html lang="en">
<head>
<meta charset="utf-8">
<title>RM Installations</title>
<link href="https://fonts.googleapis.com/css2?family=Lato:wght@400;700&family=Roboto+Condensed:wght@400;700&family=Arimo:wght@400;700&display=swap" rel="stylesheet">
<style>
:root{
  --orange:#f78f20;
  --orange-soft:rgba(247,143,32,.85);
  --ink:#222;
  --text:#444;
  --muted:#777;
  --line:#ddd;
  --panel:#f5f5f5;
  --footer:#000;
  --footer-panel:#3d3d3d;
}
*{margin:0;padding:0;box-sizing:border-box}
html,body{width:674px;height:1200px;overflow:hidden;background:#fff}
body{position:relative;font-family:'Lato',sans-serif;color:var(--text)}
.abs{position:absolute}
.topline{left:0;top:0;width:674px;height:3px;background:var(--orange)}
.header{left:0;top:3px;width:674px;height:65px;background:linear-gradient(#fff,#ececec)}
.brand{left:74px;top:14px;display:flex;align-items:center;gap:7px}
.brand-mark{width:26px;height:26px;background:var(--orange)}
.brand-name{font-family:'Arimo',sans-serif;font-size:12px;line-height:12px;color:var(--ink);text-transform:uppercase}
.phone{left:508px;top:15px;display:flex;align-items:center;gap:6px}
.phone-label{font-family:'Arimo',sans-serif;font-size:7.5px;color:var(--text)}
.phone-num{font-family:'Arimo',sans-serif;font-size:12px;color:var(--ink)}
.nav{left:74px;top:56px;width:526px;height:25px;background:#fff;border-bottom:2px solid var(--orange);display:flex;box-shadow:0 1px 3px rgba(0,0,0,.2);z-index:2}
.nav-home{width:29px;height:23px;background:var(--ink)}
.nav a{font-family:'Roboto Condensed',sans-serif;font-weight:700;font-size:8px;color:var(--ink);text-decoration:none;display:flex;align-items:center;justify-content:center;border-right:1px solid var(--line)}
.nav a:last-child{border-right:0}
.hero{left:0;top:68px;width:674px;height:250px;background:linear-gradient(#ddd8d3 0%,#8c7f77 40%,#6e6660 60%,#e8e4df 100%)}
.hero-band{left:0;top:295px;width:674px;height:23px;background:var(--orange-soft);border-bottom:2px solid var(--orange);display:flex;align-items:center;justify-content:center;font-family:'Roboto Condensed',sans-serif;font-weight:700;font-size:12px;color:#222}
.hero-arrow{top:301px;width:11px;height:11px}
.section-title{left:0;width:674px;text-align:center;font-family:'Arimo',sans-serif;font-weight:700;font-size:17px;color:var(--ink)}
.section-title span{color:var(--orange)}
.divider{left:305px;width:64px;height:1px;background:#ccc}
.intro{left:76px;top:395px;width:522px;text-align:center;font-size:7px;line-height:11.8px;color:var(--text)}
.btn{background:var(--orange);color:#fff;font-size:7.5px;display:flex;align-items:center;justify-content:center;height:18px}
.products-bg{left:0;top:495px;width:674px;height:280px;background:var(--panel);border-top:1px solid #e6e6e6;border-bottom:1px solid #e6e6e6}
.card{top:579px;width:161px;height:143px;background:#fff;border:1px solid var(--line);border-radius:2px}
.card-img{left:4px;top:5px;width:151px;height:64px}
.card-title{left:0;top:76px;width:159px;text-align:center;font-family:'Arimo',sans-serif;font-weight:700;font-size:10px;color:var(--ink)}
.card-text{left:4px;top:94px;width:151px;text-align:center;font-family:'Arimo',sans-serif;font-size:7px;line-height:11px;color:var(--text)}
.card-plus{left:142px;top:125px;width:10px;height:10px;background:var(--orange);color:#fff;font-size:10px;line-height:10px;text-align:center;font-weight:700}
.tile{overflow:hidden}
.tile-overlay{inset:0;background:rgba(0,0,0,.55);color:#fff;text-align:center}
.footer{left:0;top:1048px;width:674px;height:126px;background:var(--footer)}
.feedback{left:79px;top:1048px;width:162px;height:114px;background:var(--footer-panel)}
.feedback-title{left:5px;top:4px;font-family:'Roboto Condensed',sans-serif;font-weight:700;font-style:italic;font-size:9px;color:#fff}
.field{left:5px;width:152px;height:20px;background:#eee;border-radius:2px;font-size:6.5px;color:#888;padding-left:8px;display:flex;align-items:center}
.foot-head{font-family:'Roboto Condensed',sans-serif;font-weight:700;font-size:10px;color:#fff;padding-bottom:5px;border-bottom:1px solid #444}
.foot-link{font-size:6.5px;color:#ccc}
.contact-line{font-size:7px;color:#fff}
.bottom{left:0;top:1174px;width:674px;height:26px;background:var(--orange)}
.social{top:1179px;width:16px;height:16px;border-radius:50%;background:#fff}
.copy{right:74px;top:1183px;font-size:7px;color:#222}
</style>
</head>
<body>
<div class="abs topline"></div>
<header class="abs header"></header>
<div class="abs brand"><div class="brand-mark"></div><div class="brand-name">RM<br>Installations</div></div>
<div class="abs phone">
  <svg width="16" height="16" viewBox="0 0 16 16"><circle cx="8" cy="8" r="7" fill="none" stroke="#aaa"/><path d="M5 4l2 2-1 1c.5 1.3 1.7 2.5 3 3l1-1 2 2-1.5 1.5C7 12 4 9 3.5 5.5z" fill="#999"/></svg>
  <div><div class="phone-label">Call Us Today</div><div class="phone-num">0123456789</div></div>
</div>
<nav class="abs nav">
  <div class="nav-home"></div>
  <a href="#" style="width:79px">OUR TEAM</a>
  <a href="#" style="width:78px">PRODUCTS</a>
  <a href="#" style="width:71px">SERVICE</a>
  <a href="#" style="width:101px">PAST PROJECT</a>
  <a href="#" style="width:80px">FEEDBACK</a>
  <a href="#" style="width:88px">CONTACT US</a>
</nav>
<div class="abs hero" role="img" aria-label="Home theatre room with wall-mounted TV, speakers and white sofas"></div>
<div class="abs hero-band">Whole-House Control Systems</div>
<svg class="abs hero-arrow" style="left:78px" viewBox="0 0 11 11"><circle cx="5.5" cy="5.5" r="5.5" fill="#fff" opacity=".7"/><path d="M6.5 3L4 5.5 6.5 8z" fill="var(--orange)"/></svg>
<svg class="abs hero-arrow" style="left:584px" viewBox="0 0 11 11"><circle cx="5.5" cy="5.5" r="5.5" fill="#fff" opacity=".7"/><path d="M4.5 3L7 5.5 4.5 8z" fill="var(--orange)"/></svg>

<h1 class="abs section-title" style="top:344px">WECLOME TO <span>RM INSTALLATIONS</span></h1>
<div class="abs divider" style="top:378px"></div>
<p class="abs intro">Lorem ipsum dolor sit amet, consectetuer adipiscing elit, sed diam nonummy nibh euismod tincidunt ut laoreet dolore magna aliquam erat volutpat. Ut wisi enim ad minim veniam, quis nostrud exerci tation ullamcorper suscipit lobortis nisl ut aliquip ex ea commodo consequat. Duis autem vel eum iriure dolor in hendrerit in vulputate velit esse molestie consequat, vel illum dolore eu feugiat nulla facilisis at vero eros et accumsan et iusto odio dignissim qui blandit praesent luptatum zzril delenit augue duis dolore te feugait nulla facilisi.</p>
<a class="abs btn" style="left:305px;top:450px;width:63px">Read More »</a>

<section class="abs products-bg"></section>
<h2 class="abs section-title" style="top:520px">OUR <span>PRODUCTS</span></h2>
<div class="abs divider" style="top:554px"></div>
<svg class="abs" style="left:54px;top:640px" width="10" height="18" viewBox="0 0 10 18"><path d="M9 1L1 9l8 8" fill="none" stroke="var(--orange)" stroke-width="2"/></svg>
<svg class="abs" style="left:610px;top:640px" width="10" height="18" viewBox="0 0 10 18"><path d="M1 1l8 8-8 8" fill="none" stroke="var(--orange)" stroke-width="2"/></svg>

<div class="abs card" style="left:75px">
  <div class="abs card-img" role="img" aria-label="Dark private cinema with rows of seats" style="background:linear-gradient(#111,#3a2a1e)"></div>
  <div class="abs card-title">Residential Cinemas</div>
  <p class="abs card-text">Lorem ipsum dolor sit amet, consectetuer ullamcorper suscipit lobortis nisl ut consequat ullamcorper.</p>
  <div class="abs card-plus">+</div>
</div>
<div class="abs card" style="left:256px">
  <div class="abs card-img" role="img" aria-label="Room with lighting controlled by a handheld remote" style="background:linear-gradient(#f3f3f3,#9a9a9a)"></div>
  <div class="abs card-title">Automated Lighting Control</div>
  <p class="abs card-text">Lorem ipsum dolor sit amet, consectetuer ullamcorper suscipit lobortis nisl ut consequat ullamcorper.</p>
  <div class="abs card-plus">+</div>
</div>
<div class="abs card" style="left:439px">
  <div class="abs card-img" role="img" aria-label="Orange lounge with TV, speakers and red chairs" style="background:linear-gradient(#f0a030,#e8e0d8)"></div>
  <div class="abs card-title">Outdoor Audio and Video</div>
  <p class="abs card-text">Lorem ipsum dolor sit amet, consectetuer ullamcorper suscipit lobortis nisl ut consequat ullamcorper.</p>
  <div class="abs card-plus">+</div>
</div>
<a class="abs btn" style="left:301px;top:732px;width:63px">View More »</a>

<h2 class="abs section-title" style="top:800px;font-family:'Roboto Condensed',sans-serif">PAST <span>PROJECT</span></h2>
<div class="abs divider" style="top:832px"></div>

<div class="abs tile" style="left:0;top:862px;width:185px;height:160px;background:linear-gradient(#0a1a3a,#3a2a1a)" role="img" aria-label="Media room with blue ceiling lights and large screen"></div>
<div class="abs tile" style="left:187px;top:862px;width:134px;height:91px;background:#333" role="img" aria-label="Home cinema interior">
  <div class="abs tile-overlay">
    <div style="margin-top:28px;font-family:'Arimo',sans-serif;font-weight:700;font-size:8px">LOREM IPSUM DOLOR</div>
    <div style="margin:5px 14px 0;font-size:6px;line-height:8px">Mauris ultrices lorem et felis vehicula efficitur. Suspendisse pellentesque.</div>
  </div>
</div>
<div class="abs tile" style="left:187px;top:956px;width:134px;height:66px;background:linear-gradient(#111,#4a3320)" role="img" aria-label="Cinema seating rows"></div>
<div class="abs tile" style="left:322px;top:862px;width:190px;height:75px;background:linear-gradient(135deg,#c9c4be,#b0402a 55%,#ddd)" role="img" aria-label="Desk with two monitors"></div>
<div class="abs tile" style="left:322px;top:940px;width:102px;height:82px;background:linear-gradient(#bbb,#222)" role="img" aria-label="Equipment rack"></div>
<div class="abs tile" style="left:426px;top:940px;width:86px;height:82px;background:linear-gradient(#e6ddd0,#9a8f80)" role="img" aria-label="Cabinet with AV components"></div>
<div class="abs tile" style="left:514px;top:862px;width:160px;height:160px;background:linear-gradient(#e2d6c4,#7a6a58)" role="img" aria-label="Ceiling-mounted projector"></div>

<footer class="abs footer"></footer>
<div class="abs feedback">
  <div class="abs feedback-title">Feedback</div>
  <div class="abs field" style="top:35px">Name</div>
  <div class="abs field" style="top:62px">Email</div>
  <a class="abs btn" style="left:5px;top:90px;width:53px;height:15px">Subscribe</a>
</div>
<div class="abs" style="left:265px;top:1057px;width:110px"><div class="foot-head">Quick Links</div></div>
<div class="abs foot-link" style="left:265px;top:1081px;line-height:13.6px">Home<br>Our Team<br>Services<br>Past Project</div>
<div class="abs foot-link" style="left:328px;top:1081px;line-height:13.6px">Feedback<br>Contact Us<br>Products</div>
<div class="abs" style="left:400px;top:1057px;width:190px"><div class="foot-head">Contact Info</div></div>
<div class="abs" style="left:400px;top:1076px;width:80px;height:76px;background:#1a1a1a" role="img" aria-label="World map"></div>
<div class="abs" style="left:476px;top:1081px;width:114px;height:34px;background:#111"></div>
<svg class="abs" style="left:462px;top:1084px" width="11" height="15" viewBox="0 0 11 15"><path d="M5.5 0A5.5 5.5 0 0 0 0 5.5C0 10 5.5 15 5.5 15S11 10 11 5.5A5.5 5.5 0 0 0 5.5 0z" fill="#fff"/><circle cx="5.5" cy="5.5" r="2" fill="#000"/></svg>
<div class="abs contact-line" style="left:486px;top:1087px;line-height:10px">123,Lorem Ipsum is simply<br>dummy text of the printing</div>
<svg class="abs" style="left:463px;top:1120px" width="10" height="10" viewBox="0 0 16 16"><path d="M3 1l3 3-1.5 1.5c.8 2 2.5 3.7 4.5 4.5L10.5 8.5l3 3L11 14C6 13 2 9 1.5 4z" fill="#fff"/></svg>
<div class="abs contact-line" style="left:480px;top:1121px">0123 4567 891</div>
<svg class="abs" style="left:463px;top:1139px" width="10" height="8" viewBox="0 0 10 8"><rect x=".5" y=".5" width="9" height="7" fill="none" stroke="#fff"/><path d="M.5.5L5 4.5 9.5.5" fill="none" stroke="#fff"/></svg>
<div class="abs contact-line" style="left:480px;top:1138px">info@rminstallations.com</div>

<div class="abs bottom"></div>
<div class="abs social" style="left:75px;background:#111" aria-label="Social link"></div>
<div class="abs social" style="left:99px" aria-label="Social link"></div>
<div class="abs social" style="left:122px" aria-label="Social link"></div>
<div class="abs social" style="left:146px" aria-label="Social link"></div>
<div class="abs copy">© 2015 RM Installations. All Rights Reserved.</div>
</body>
</html>
```